holloway paving service

Needs to have phone number 0418259730 and email markholloway@brightmail.com.au.
ABN 62318470915
name mark holloway

For all your concreting solutions
Excavation
Exposed & colour concrete
House & shed slabs
Driveways
Landing & steps

Contact Information for Business Card

ph 0418259730
email markholloway@brightmail.com.au.
ABN 62318470915
name mark holloway

```html
<!DOCTYPE html>
<html lang="en">
<head>
<meta charset="utf-8">
<title>Holloway Paving Service – Business Card</title>
<link rel="stylesheet" href="https://fonts.googleapis.com/css2?family=Montserrat:wght@500;600;700&family=Nunito:wght@400;600&display=swap">
<style>
  :root {
    --orange: #f26a21;
    --orange-deep: #e35d17;
    --orange-light: #f58a4c;
    --grey: #5f5f5f;
    --grey-text: #555555;
    --silver-1: #f4f4f4;
    --silver-2: #e2e2e2;
    --white: #ffffff;
    --page: #ececec;
  }
  * { box-sizing: border-box; margin: 0; padding: 0; }
  html, body { width: 1200px; height: 960px; overflow: hidden; }
  body {
    background: var(--page);
    font-family: "Nunito", sans-serif;
    position: relative;
  }
  .card {
    position: absolute;
    width: 600px;
    height: 341px;
    overflow: hidden;
    box-shadow: 0 4px 14px rgba(0,0,0,0.18);
  }

  /* Front */
  .card-front {
    left: 302px; top: 127px;
    background: linear-gradient(135deg, var(--silver-2) 0%, var(--silver-1) 55%, var(--silver-2) 100%);
  }
  .front-panel { position: absolute; left: 0; top: 0; }
  .brand-mark {
    position: absolute;
    left: 26px; top: 152px;
    display: flex; align-items: center; gap: 10px;
    font-family: "Montserrat", sans-serif;
    font-weight: 700;
    font-size: 17px;
    letter-spacing: 1px;
    color: var(--white);
  }
  .brand-square { width: 16px; height: 16px; background: var(--white); flex-shrink: 0; }

  .company {
    position: absolute; right: 38px; top: 38px;
    text-align: right;
    font-family: "Montserrat", sans-serif;
  }
  .company-name {
    font-weight: 700; font-size: 21px; color: var(--orange);
    letter-spacing: 0.2px; line-height: 1.1;
  }
  .company-sub {
    display: flex; align-items: center; justify-content: flex-end; gap: 8px;
    margin-top: 2px;
  }
  .company-sub .rule { width: 52px; height: 2px; background: var(--grey); }
  .company-sub .word {
    font-weight: 600; font-size: 16px; color: var(--grey);
    letter-spacing: 2.5px; line-height: 1.1;
  }
  .phone {
    font-weight: 500; font-size: 16px; color: var(--orange);
    letter-spacing: 2px; margin-right: 62px; line-height: 1.1;
  }

  .person {
    position: absolute; right: 38px; top: 238px;
    text-align: right;
  }
  .person-name {
    font-family: "Montserrat", sans-serif;
    font-weight: 700; font-size: 21px; color: var(--orange);
    line-height: 1.2;
  }
  .person-line { font-size: 14.5px; color: var(--grey-text); line-height: 1.45; }
  .person-line.abn { letter-spacing: 0.6px; }

  /* Back */
  .card-back {
    left: 299px; top: 500px;
    background: linear-gradient(100deg, var(--orange-deep) 0%, var(--orange-light) 40%, var(--orange) 100%);
  }
  .back-mark {
    position: absolute; left: 120px; top: 146px;
    width: 100px;
    display: flex; flex-direction: column; align-items: center; gap: 8px;
    font-family: "Montserrat", sans-serif;
    font-weight: 700; font-size: 14px; letter-spacing: 1px;
    color: var(--white);
  }
  .back-mark .brand-square { width: 18px; height: 18px; }
  .services {
    position: absolute; left: 254px; top: 125px;
    list-style: none;
    font-family: "Nunito", sans-serif;
    font-size: 14.5px; color: var(--white);
    line-height: 18px;
  }
  .services li { display: flex; align-items: center; gap: 6px; }
  .services li::before {
    content: ""; width: 5px; height: 5px; background: var(--white);
    transform: rotate(45deg); flex-shrink: 0;
  }
  .tagline {
    position: absolute; left: 0; right: 0; bottom: 34px;
    text-align: center;
    font-family: "Montserrat", sans-serif;
    font-weight: 600; font-size: 13px; letter-spacing: 1.5px;
    color: var(--white);
    text-transform: uppercase;
  }
</style>
</head>
<body>

<section class="card card-front" aria-label="Business card front">
  <svg class="front-panel" width="600" height="341" viewBox="0 0 600 341" aria-hidden="true">
    <polygon points="0,0 200,0 168,341 0,341" fill="var(--orange)"/>
  </svg>
  <div class="brand-mark"><span class="brand-square"></span>HOLLOWAY</div>

  <div class="company">
    <div class="company-name">HOLLOWAY PAVING</div>
    <div class="company-sub"><span class="rule"></span><span class="word">SERVICE</span><span class="rule"></span></div>
    <div class="phone">0418259730</div>
  </div>

  <div class="person">
    <div class="person-name">MARK HOLLOWAY</div>
    <div class="person-line">markholloway@brightmail.com.au</div>
    <div class="person-line abn">ABN 62318470915</div>
  </div>
</section>

<section class="card card-back" role="img" aria-label="Business card back with repeating brand pattern on orange">
  <div class="back-mark"><span class="brand-square"></span>HOLLOWAY</div>
  <ul class="services">
    <li>Excavation</li>
    <li>Exposed &amp; colour concrete</li>
    <li>House &amp; shed slabs</li>
    <li>Driveways</li>
    <li>Landing &amp; steps</li>
  </ul>
  <p class="tagline">For all your concreting solutions</p>
</section>

</body>
</html>
```